Nivel Crest - Powerpoint Templates

We are a consultancy to help builders to optimize their planning in order to save building costs. For that reason we need templates for teasers and presentations where we offer our services, show our team and their capacities and present workflows, organization charts, price lists etc.

```html
<!DOCTYPE html>
<html lang="en">
<head>
<meta charset="utf-8">
<title>Nivel Crest – Presentation Template</title>
<link href="https://fonts.googleapis.com/css2?family=Montserrat:wght@400;500;600;700&family=Oswald:wght@600;700&display=swap" rel="stylesheet">
<style>
:root{
  --stage:#e0b45c;
  --paper:#ffffff;
  --gold:#c8952f;
  --gold-light:#ecc96f;
  --gold-dark:#8f621a;
  --ink:#1d1d1d;
  --grey:#6f6f6f;
  --dark:#2b2b2e;
  --rule:#d8d8d8;
}
*{box-sizing:border-box;margin:0;padding:0}
html,body{width:1104px;height:1200px;overflow:hidden}
body{background:var(--stage);font-family:"Montserrat",sans-serif;color:var(--ink);position:relative}
.slide{position:absolute;width:261px;height:163px;background:var(--paper);overflow:hidden}
.heading{position:absolute;left:10px;top:7px;font-size:7.5px;font-weight:500;color:var(--ink)}
.heading b{color:var(--gold);font-weight:500}
.body-text{font-size:2.4px;line-height:3.3px;text-align:justify;color:var(--ink)}
.title-sm{font-size:4.4px;font-weight:600;color:var(--ink)}
.title-gold{font-size:4.6px;font-weight:600;color:var(--gold)}
.footer{position:absolute;left:0;right:0;top:148px;height:6px;display:flex;align-items:center}
.footer .mark{width:6px;height:6px;background:var(--gold)}
.footer .brand{font-size:3px;font-weight:700;color:var(--gold-dark);margin:0 3px 0 4px;width:40px}
.footer .bar{flex:1;height:6px;background:linear-gradient(90deg,var(--gold-dark),var(--gold-light) 45%,var(--gold));display:flex;align-items:center;justify-content:space-between;padding:0 8px 0 65px;font-size:2.4px;color:#fff}
.logo{position:absolute;left:0;width:261px;display:flex;align-items:center;justify-content:center;gap:5px}
.logo .sq{width:12px;height:12px;background:var(--gold)}
.logo .name{font-size:11px;font-weight:700;color:var(--gold);line-height:1}
.photo{position:absolute;background:linear-gradient(180deg,#9c7a3e,#6e5427 55%,#b8944f)}
.cols2{position:absolute;display:grid;grid-template-columns:1fr 1fr;column-gap:10px}
.dot{border-radius:50%;display:inline-block;flex:none;position:relative}
.dot::after{content:"";position:absolute;left:30%;top:38%;width:40%;height:30%;border-radius:1px;background:#fff}
.dot.g{background:radial-gradient(circle at 40% 35%,var(--gold-light),var(--gold) 60%,var(--gold-dark))}
.dot.d{background:radial-gradient(circle at 40% 35%,#777,#2a2a2a 65%)}
.item{display:flex;gap:5px;align-items:flex-start}
.hex{width:14px;height:14px;flex:none;background:var(--gold);clip-path:polygon(25% 5%,75% 5%,100% 50%,75% 95%,25% 95%,0 50%);position:relative}
.hex::after{content:"";position:absolute;left:32%;top:28%;width:36%;height:36%;border:1px solid #fff;border-radius:50%}
ul.bullets{list-style:none}
ul.bullets li{position:relative;padding-left:4px;margin-bottom:4px}
ul.bullets li::before{content:"";position:absolute;left:0;top:1px;width:1.5px;height:1.5px;background:var(--ink)}
table.data{border-collapse:collapse;font-size:2.6px;width:100%}
table.data th{background:#8d8d8d;color:#fff;font-weight:500;height:11px;text-align:center}
table.data th:first-child{text-align:left;padding-left:3px}
table.data td{height:10.8px;border-bottom:.5px solid var(--rule);text-align:center}
table.data td:first-child{text-align:left;padding-left:3px}
</style>
</head>
<body>

<!-- 1 Cover -->
<section class="slide" style="left:111px;top:104px">
  <div class="logo" style="top:14px"><span class="sq"></span><span class="name">NIVEL CREST</span></div>
  <div class="photo" role="img" aria-label="City skyline photograph in golden tones" style="left:0;top:41px;width:261px;height:82px"></div>
  <div style="position:absolute;left:0;width:261px;top:100px;text-align:center;font-family:'Oswald',sans-serif;font-weight:700;font-size:20px;color:#fff;line-height:1">PRESENTATION</div>
  <div style="position:absolute;left:0;width:261px;top:122px;text-align:center;font-family:'Oswald',sans-serif;font-weight:700;font-size:19px;color:var(--gold);line-height:1">TITLE GOESHERE</div>
  <div style="position:absolute;left:0;width:261px;top:145px;text-align:center;font-size:5.2px">Subtitle of Presentation Goes Here</div>
</section>

<!-- 2 Two-column text -->
<section class="slide" style="left:421px;top:104px">
  <div class="heading"><b>Heading</b> Goes Here</div>
  <div class="cols2 body-text" style="left:18px;top:35px;width:228px">
    <div><p>Lorem ipsum dolor sit amet, consectetuer adipiscing elit, sed diam nonummy nibh euismod tincidunt ut laoreet dolore magna aliquam erat volutpat. Ut wisi enim ad minim veniam, quis nostrud exerci tation ullamcorper suscipit lobortis nisl ut aliquip.</p><p style="margin-top:5px">Lorem ipsum dolor sit amet, consectetuer adipiscing elit, sed diam nonummy nibh euismod tincidunt ut laoreet dolore magna aliquam erat volutpat. Ut wisi enim ad minim veniam, quis nostrud exerci tation ullamcorper.</p><p style="margin-top:5px">Lorem ipsum dolor sit amet, consectetuer adipiscing elit, sed diam nonummy nibh euismod tincidunt ut laoreet dolore magna aliquam erat volutpat. Ut wisi enim ad minim veniam, quis nostrud exerci tation ullamcorper suscipit lobortis nisl ut aliquip ex ea commodo consequat. Duis autem vel eum iriure dolor in hendrerit in vulputate velit esse.</p></div>
    <div><p>Lorem ipsum dolor sit amet, consectetuer adipiscing elit, sed diam nonummy nibh euismod tincidunt ut laoreet dolore magna aliquam erat volutpat. Ut wisi enim ad minim veniam, quis nostrud exerci tation ullamcorper suscipit lobortis nisl ut aliquip.</p><p style="margin-top:5px">Lorem ipsum dolor sit amet, consectetuer adipiscing elit, sed diam nonummy nibh euismod tincidunt ut laoreet dolore magna aliquam erat volutpat. Ut wisi enim ad minim veniam, quis nostrud exerci tation ullamcorper.</p><p style="margin-top:5px">Lorem ipsum dolor sit amet, consectetuer adipiscing elit, sed diam nonummy nibh euismod tincidunt ut laoreet dolore magna aliquam erat volutpat. Ut wisi enim ad minim veniam, quis nostrud exerci tation ullamcorper suscipit lobortis nisl ut aliquip ex ea commodo consequat. Duis autem vel eum iriure dolor in hendrerit in vulputate velit esse.</p></div>
  </div>
  <div class="footer"><span class="mark"></span><span class="brand">NIVEL CREST</span><div class="bar"><span>www.nivelcrest.com</span><span>PAGE 01</span></div></div>
</section>

<!-- 3 Mission / Vision -->
<section class="slide" style="left:731px;top:104px">
  <div style="position:absolute;left:12px;top:24px;font-size:12px;font-weight:600;line-height:11px">OUR MISSION<br><span style="color:var(--gold)">OUR VISION</span></div>
  <div class="body-text" style="position:absolute;left:12px;top:57px;width:109px"><p>Lorem ipsum dolor sit amet, consectetuer adipiscing elit, sed diam nonummy nibh euismod tincidunt ut laoreet dolore magna aliquam erat volutpat. Ut wisi enim ad minim veniam, quis nostrud exerci tation ullamcorper.</p><p style="margin-top:6px">Lorem ipsum dolor sit amet, consectetuer adipiscing elit, sed diam nonummy nibh euismod tincidunt ut laoreet dolore magna aliquam erat volutpat. Ut wisi enim ad minim veniam, quis nostrud exerci tation ullamcorper suscipit lobortis nisl ut aliquip ex ea commodo consequat. Duis autem vel eum iriure dolor in hendrerit.</p></div>
  <div style="position:absolute;left:142px;top:32px;width:119px;height:39px;background:linear-gradient(90deg,var(--gold-dark),var(--gold-light) 50%,var(--gold));clip-path:polygon(6% 0,100% 0,100% 100%,6% 100%,0 50%)"></div>
  <div class="hex" style="position:absolute;left:128px;top:38px;width:28px;height:28px;background:var(--dark)"></div>
  <div style="position:absolute;left:161px;top:36px;width:94px;color:#fff"><div style="font-size:3.6px;font-weight:600">Title Goes Here</div><div class="body-text" style="color:#fff">Lorem ipsum dolor sit amet, consectetuer adipiscing elit, sed diam nonummy nibh euismod tincidunt ut laoreet dolore magna aliquam erat volutpat. Ut wisi enim ad minim veniam.</div></div>
  <div style="position:absolute;left:142px;top:92px;width:119px;height:39px;background:linear-gradient(90deg,#1e1e20,#55555a 60%,#2a2a2d);clip-path:polygon(6% 0,100% 0,100% 100%,6% 100%,0 50%)"></div>
  <div class="hex" style="position:absolute;left:128px;top:98px;width:28px;height:28px"></div>
  <div style="position:absolute;left:161px;top:96px;width:94px;color:#fff"><div style="font-size:3.6px;font-weight:600">Title Goes Here</div><div class="body-text" style="color:#fff">Lorem ipsum dolor sit amet, consectetuer adipiscing elit, sed diam nonummy nibh euismod tincidunt ut laoreet dolore magna aliquam erat volutpat. Ut wisi enim ad minim veniam.</div></div>
  <div class="footer"><span class="mark"></span><span class="brand">NIVEL CREST</span><div class="bar"><span>www.nivelcrest.com</span><span>PAGE 01</span></div></div>
</section>

<!-- 4 Services -->
<section class="slide" style="left:111px;top:315px">
  <div class="heading"><b>Heading</b> Goes Here</div>
  <div style="position:absolute;left:10px;top:27px;width:243px">
    <div class="title-gold" style="font-weight:500;margin-bottom:3px">Service Title Goes Here</div>
    <p class="body-text">Lorem ipsum dolor sit amet, consectetuer adipiscing elit, sed diam nonummy nibh euismod tincidunt ut laoreet dolore magna aliquam erat volutpat. Ut wisi enim ad minim veniam, quis nostrud exerci tation ullamcorper suscipit lobortis nisl ut aliquip ex ea commodo consequat. Duis autem vel eum iriure dolor in hendrerit in vulputate velit esse molestie consequat, vel illum dolore eu feugiat nulla facilisis at vero eros et accumsan et iusto odio dignissim qui blandit praesent luptatum zzril.</p>
    <p class="body-text" style="margin-top:3px">Lorem ipsum dolor sit amet, consectetuer adipiscing elit, sed diam nonummy nibh euismod tincidunt ut laoreet dolore magna aliquam erat volutpat. Ut wisi enim ad minim veniam, quis nostrud exerci tation ullamcorper suscipit lobortis nisl ut aliquip ex ea commodo consequat. Duis autem vel eum iriure dolor in hendrerit in vulputate velit esse molestie consequat, vel illum dolore eu feugiat nulla facilisis at vero eros et accumsan et iusto odio dignissim qui blandit praesent luptatum zzril delenit augue duis dolore te feugait nulla facilisi.</p>
    <div class="title-gold" style="font-weight:500;margin:4px 0 3px">Service Title Goes Here</div>
    <p class="body-text">Lorem ipsum dolor sit amet, consectetuer adipiscing elit, sed diam nonummy nibh euismod tincidunt ut laoreet dolore magna aliquam erat volutpat. Ut wisi enim ad minim veniam, quis nostrud exerci tation ullamcorper suscipit lobortis nisl ut aliquip ex ea commodo consequat. Duis autem vel eum iriure dolor in hendrerit in vulputate velit esse molestie consequat, vel illum dolore eu feugiat nulla facilisis at vero eros et accumsan et iusto odio dignissim qui blandit praesent luptatum zzril delenit augue duis dolore.</p>
  </div>
  <div class="footer"><span class="mark"></span><span class="brand">NIVEL CREST</span><div class="bar"><span>www.nivelcrest.com</span><span>PAGE 01</span></div></div>
</section>

<!-- 5 Six features -->
<section class="slide" style="left:421px;top:315px">
  <div class="heading"><b>Heading</b> Goes Here</div>
  <div class="cols2" style="left:10px;top:45px;width:243px;row-gap:15px">
    <div class="item"><span class="dot d" style="width:17px;height:17px"></span><div><div class="title-sm" style="font-weight:500">Title Goes Here</div><div class="body-text">Lorem ipsum dolor sit amet, consectetuer adipiscing elit, sed diam nonummy nibh euismod tincidunt ut laoreet dolore magna aliquam erat volutpat.</div></div></div>
    <div class="item"><span class="dot d" style="width:17px;height:17px"></span><div><div class="title-sm" style="font-weight:500">Title Goes Here</div><div class="body-text">Lorem ipsum dolor sit amet, consectetuer adipiscing elit, sed diam nonummy nibh euismod tincidunt ut laoreet dolore magna aliquam erat volutpat.</div></div></div>
    <div class="item"><span class="dot g" style="width:17px;height:17px"></span><div><div class="title-sm" style="font-weight:500">Title Goes Here</div><div class="body-text">Lorem ipsum dolor sit amet, consectetuer adipiscing elit, sed diam nonummy nibh euismod tincidunt ut laoreet dolore magna aliquam erat volutpat.</div></div></div>
    <div class="item"><span class="dot g" style="width:17px;height:17px"></span><div><div class="title-sm" style="font-weight:500">Title Goes Here</div><div class="body-text">Lorem ipsum dolor sit amet, consectetuer adipiscing elit, sed diam nonummy nibh euismod tincidunt ut laoreet dolore magna aliquam erat volutpat.</div></div></div>
    <div class="item"><span class="dot d" style="width:17px;height:17px"></span><div><div class="title-sm" style="font-weight:500">Title Goes Here</div><div class="body-text">Lorem ipsum dolor sit amet, consectetuer adipiscing elit, sed diam nonummy nibh euismod tincidunt ut laoreet dolore magna aliquam erat volutpat.</div></div></div>
    <div class="item"><span class="dot d" style="width:17px;height:17px"></span><div><div class="title-sm" style="font-weight:500">Title Goes Here</div><div class="body-text">Lorem ipsum dolor sit amet, consectetuer adipiscing elit, sed diam nonummy nibh euismod tincidunt ut laoreet dolore magna aliquam erat volutpat.</div></div></div>
  </div>
  <div class="footer"><span class="mark"></span><span class="brand">NIVEL CREST</span><div class="bar"><span>www.nivelcrest.com</span><span>PAGE 01</span></div></div>
</section>

<!-- 6 Text + hex list -->
<section class="slide" style="left:731px;top:315px">
  <div class="heading"><b>Heading</b> Goes Here</div>
  <div class="body-text" style="position:absolute;left:12px;top:36px;width:94px"><p>Lorem ipsum dolor sit amet, consectetuer adipiscing elit, sed diam nonummy nibh euismod tincidunt ut laoreet dolore magna aliquam erat volutpat. Ut wisi enim ad minim veniam, quis nostrud exerci tation ullamcorper.</p><p style="margin-top:7px">Lorem ipsum dolor sit amet, consectetuer adipiscing elit, sed diam nonummy nibh euismod tincidunt ut laoreet dolore magna aliquam erat volutpat. Ut wisi enim ad minim veniam, quis nostrud exerci tation ullamcorper.</p><p style="margin-top:7px">Lorem ipsum dolor sit amet, consectetuer adipiscing elit, sed diam nonummy nibh euismod tincidunt ut laoreet dolore magna aliquam erat volutpat. Ut wisi enim ad minim veniam, quis nostrud exerci tation ullamcorper.</p></div>
  <div style="position:absolute;left:132px;top:31px;width:120px;display:grid;row-gap:9px">
    <div class="item"><span class="hex" style="width:22px;height:22px"></span><div><div class="title-gold" style="font-weight:500">Title Goes Here</div><div class="body-text">Lorem ipsum dolor sit amet, consectetuer adipiscing elit, sed diam nonummy nibh euismod tincidunt ut laoreet.</div></div></div>
    <div class="item"><span class="hex" style="width:22px;height:22px"></span><div><div class="title-gold" style="font-weight:500">Title Goes Here</div><div class="body-text">Lorem ipsum dolor sit amet, consectetuer adipiscing elit, sed diam nonummy nibh euismod tincidunt ut laoreet.</div></div></div>
    <div class="item"><span class="hex" style="width:22px;height:22px"></span><div><div class="title-gold" style="font-weight:500">Title Goes Here</div><div class="body-text">Lorem ipsum dolor sit amet, consectetuer adipiscing elit, sed diam nonummy nibh euismod tincidunt ut laoreet.</div></div></div>
    <div class="item"><span class="hex" style="width:22px;height:22px"></span><div><div class="title-gold" style="font-weight:500">Title Goes Here</div><div class="body-text">Lorem ipsum dolor sit amet, consectetuer adipiscing elit, sed diam nonummy nibh euismod tincidunt ut laoreet.</div></div></div>
  </div>
  <div class="footer"><span class="mark"></span><span class="brand">NIVEL CREST</span><div class="bar"><span>www.nivelcrest.com</span><span>PAGE 01</span></div></div>
</section>

<!-- 7 Six gold items -->
<section class="slide" style="left:111px;top:517px">
  <div class="heading"><b>Heading</b> Goes Here</div>
  <div class="cols2" style="left:10px;top:41px;width:243px;row-gap:14px">
    <div class="item"><span class="dot g" style="width:18px;height:18px"></span><div style="border-left:.5px solid var(--rule);padding-left:4px"><div class="title-sm" style="font-weight:500">Title Goes Here</div><div class="body-text" style="font-size:3px;line-height:4px">Lorem ipsum dolor sit amet, consectetuer adipiscing elit, sed diam nonummy nibh euismod tincidunt ut laoreet dolore magna</div></div></div>
    <div class="item"><span class="dot g" style="width:18px;height:18px"></span><div style="border-left:.5px solid var(--rule);padding-left:4px"><div class="title-sm" style="font-weight:500">Title Goes Here</div><div class="body-text" style="font-size:3px;line-height:4px">Lorem ipsum dolor sit amet, consectetuer adipiscing elit, sed diam nonummy nibh euismod tincidunt ut laoreet dolore magna</div></div></div>
    <div class="item"><span class="dot g" style="width:18px;height:18px"></span><div style="border-left:.5px solid var(--rule);padding-left:4px"><div class="title-sm" style="font-weight:500">Title Goes Here</div><div class="body-text" style="font-size:3px;line-height:4px">Lorem ipsum dolor sit amet, consectetuer adipiscing elit, sed diam nonummy nibh euismod tincidunt ut laoreet dolore magna</div></div></div>
    <div class="item"><span class="dot g" style="width:18px;height:18px"></span><div style="border-left:.5px solid var(--rule);padding-left:4px"><div class="title-sm" style="font-weight:500">Title Goes Here</div><div class="body-text" style="font-size:3px;line-height:4px">Lorem ipsum dolor sit amet, consectetuer adipiscing elit, sed diam nonummy nibh euismod tincidunt ut laoreet dolore magna</div></div></div>
    <div class="item"><span class="dot g" style="width:18px;height:18px"></span><div style="border-left:.5px solid var(--rule);padding-left:4px"><div class="title-sm" style="font-weight:500">Title Goes Here</div><div class="body-text" style="font-size:3px;line-height:4px">Lorem ipsum dolor sit amet, consectetuer adipiscing elit, sed diam nonummy nibh euismod tincidunt ut laoreet dolore magna</div></div></div>
    <div class="item"><span class="dot g" style="width:18px;height:18px"></span><div style="border-left:.5px solid var(--rule);padding-left:4px"><div class="title-sm" style="font-weight:500">Title Goes Here</div><div class="body-text" style="font-size:3px;line-height:4px">Lorem ipsum dolor sit amet, consectetuer adipiscing elit, sed diam nonummy nibh euismod tincidunt ut laoreet dolore magna</div></div></div>
  </div>
  <div class="footer"><span class="mark"></span><span class="brand">NIVEL CREST</span><div class="bar"><span>www.nivelcrest.com</span><span>PAGE 01</span></div></div>
</section>

<!-- 8 Team -->
<section class="slide" style="left:421px;top:517px">
  <div style="position:absolute;left:0;width:261px;top:20px;text-align:center;font-size:12px;font-weight:600">OUR CREATIVE TEAM</div>
  <div class="body-text" style="position:absolute;left:35px;top:36px;width:191px;text-align:center">Lorem ipsum dolor sit amet, consectetuer adipiscing elit, sed diam nonummy nibh euismod tincidunt ut laoreet dolore magna aliquam erat volutpat. Ut wisi enim ad minim veniam, quis nostrud exerci tation ullamcorper suscipit lobortis nisl ut aliquip ex ea commodo consequat.</div>
  <div style="position:absolute;left:20px;top:58px;width:221px;display:grid;grid-template-columns:repeat(4,1fr);column-gap:8px;text-align:center">
    <div><div role="img" aria-label="Team member portrait" style="width:49px;height:49px;margin:0 auto;border-radius:50%;background:radial-gradient(circle at 40% 35%,var(--gold-light),var(--gold) 60%,var(--gold-dark))"></div><div style="font-size:4.4px;font-weight:500;margin-top:5px">Name Here</div><div class="body-text" style="text-align:center">Lorem ipsum dolor sit amet, consectetuer adipiscing elit, sed diam nonummy nibh euismod tincidunt ut laoreet dolore magna.</div></div>
    <div><div role="img" aria-label="Team member portrait" style="width:49px;height:49px;margin:0 auto;border-radius:50%;background:radial-gradient(circle at 40% 35%,var(--gold-light),var(--gold) 60%,var(--gold-dark))"></div><div style="font-size:4.4px;font-weight:500;margin-top:5px">Name Here</div><div class="body-text" style="text-align:center">Lorem ipsum dolor sit amet, consectetuer adipiscing elit, sed diam nonummy nibh euismod tincidunt ut laoreet dolore magna.</div></div>
    <div><div role="img" aria-label="Team member portrait" style="width:49px;height:49px;margin:0 auto;border-radius:50%;background:radial-gradient(circle at 40% 35%,var(--gold-light),var(--gold) 60%,var(--gold-dark))"></div><div style="font-size:4.4px;font-weight:500;margin-top:5px">Name Here</div><div class="body-text" style="text-align:center">Lorem ipsum dolor sit amet, consectetuer adipiscing elit, sed diam nonummy nibh euismod tincidunt ut laoreet dolore magna.</div></div>
    <div><div role="img" aria-label="Team member portrait" style="width:49px;height:49px;margin:0 auto;border-radius:50%;background:radial-gradient(circle at 40% 35%,var(--gold-light),var(--gold) 60%,var(--gold-dark))"></div><div style="font-size:4.4px;font-weight:500;margin-top:5px">Name Here</div><div class="body-text" style="text-align:center">Lorem ipsum dolor sit amet, consectetuer adipiscing elit, sed diam nonummy nibh euismod tincidunt ut laoreet dolore magna.</div></div>
  </div>
  <div class="footer"><span class="mark"></span><span class="brand">NIVEL CREST</span><div class="bar"><span>www.nivelcrest.com</span><span>PAGE 01</span></div></div>
</section>

<!-- 9 Table -->
<section class="slide" style="left:731px;top:517px">
  <div class="heading"><b>Heading</b> Goes Here</div>
  <div style="position:absolute;left:84px;top:34px;width:42px;height:95px;border:.8px solid var(--gold);border-radius:3px"></div>
  <div style="position:absolute;left:12px;top:38px;width:238px">
    <table class="data">
      <tr><th style="width:30%">Heading Goes Here</th><th style="background:var(--gold)">Heading<br>Goes Here</th><th>Heading<br>Goes Here</th><th>Heading<br>Goes Here</th><th>Heading<br>Goes Here</th></tr>
      <tr><td>Lorem Ipsum Goes Here</td><td>23</td><td>12</td><td>78</td><td>12</td></tr>
      <tr><td>Lorem Ipsum Goes Here</td><td>45</td><td>56</td><td>12</td><td>56</td></tr>
      <tr><td>Lorem Ipsum Goes Here</td><td>78</td><td>76</td><td>34</td><td>76</td></tr>
      <tr><td>Lorem Ipsum Goes Here</td><td>22</td><td>12</td><td>55</td><td>12</td></tr>
      <tr><td>Lorem Ipsum Goes Here</td><td>34</td><td>66</td><td>45</td><td>66</td></tr>
      <tr><td>Lorem Ipsum Goes Here</td><td>67</td><td>47</td><td>78</td><td>47</td></tr>
      <tr><td>Lorem Ipsum Goes Here</td><td>87</td><td>67</td><td>12</td><td>67</td></tr>
    </table>
  </div>
  <div class="footer"><span class="mark"></span><span class="brand">NIVEL CREST</span><div class="bar"><span>www.nivelcrest.com</span><span>PAGE 01</span></div></div>
</section>

<!-- 10 Bullet columns -->
<section class="slide" style="left:111px;top:711px">
  <div class="heading"><b>Heading</b> Goes Here</div>
  <div class="cols2" style="left:11px;top:35px;width:241px">
    <div><div class="title-gold" style="margin-bottom:6px">Curabitur Dapibus Dignissim Dui.</div><ul class="bullets body-text"><li>Lorem ipsum dolor sit amet, consectetuer adipiscing elit, sed diam nonummy nibh euismod tincidunt ut laoreet dolore magna aliquam erat volutpat. Ut wisi enim ad minim veniam.</li><li>Lorem ipsum dolor sit amet, consectetuer adipiscing elit, sed diam nonummy nibh euismod tincidunt ut laoreet dolore magna aliquam erat volutpat. Ut wisi enim ad minim veniam, quis nostrud exerci tation ullamcorper suscipit lobortis nisl ut aliquip ex ea commodo consequat.</li><li>Lorem ipsum dolor sit amet, consectetuer adipiscing elit, sed diam nonummy nibh euismod tincidunt ut laoreet dolore magna aliquam erat volutpat. Ut wisi enim ad minim veniam, quis nostrud exerci tation ullamcorper suscipit lobortis nisl ut aliquip ex ea commodo consequat.</li></ul></div>
    <div><div class="title-gold" style="margin-bottom:6px">Curabitur Dapibus Dignissim Dui.</div><ul class="bullets body-text"><li>Lorem ipsum dolor sit amet, consectetuer adipiscing elit, sed diam nonummy nibh euismod tincidunt ut laoreet dolore magna aliquam erat volutpat. Ut wisi enim ad minim veniam.</li><li>Lorem ipsum dolor sit amet, consectetuer adipiscing elit, sed diam nonummy nibh euismod tincidunt ut laoreet dolore magna aliquam erat volutpat. Ut wisi enim ad minim veniam, quis nostrud exerci tation ullamcorper suscipit lobortis nisl ut aliquip ex ea commodo consequat.</li><li>Lorem ipsum dolor sit amet, consectetuer adipiscing elit, sed diam nonummy nibh euismod tincidunt ut laoreet dolore magna aliquam erat volutpat. Ut wisi enim ad minim veniam, quis nostrud exerci tation ullamcorper suscipit lobortis nisl ut aliquip ex ea commodo consequat.</li></ul></div>
  </div>
  <div class="footer"><span class="mark"></span><span class="brand">NIVEL CREST</span><div class="bar"><span>www.nivelcrest.com</span><span>PAGE 01</span></div></div>
</section>

<!-- 11 Cards + bullets -->
<section class="slide" style="left:421px;top:718px">
  <div class="heading"><b>Heading</b> Goes Here</div>
  <div style="position:absolute;left:14px;top:46px;width:56px;height:88px;border-radius:9px 9px 0 0;background:linear-gradient(180deg,var(--gold-light),var(--gold) 50%,var(--gold-dark));border-bottom:2px solid var(--dark);color:#fff;text-align:center;padding-top:7px">
    <span class="dot d" style="width:10px;height:10px"></span><div style="font-size:5.4px;margin:4px 0 3px">Heading</div><div class="body-text" style="color:#fff;text-align:center;padding:0 4px">Lorem ipsum dolor sit amet, consectetuer adipiscing elit, sed diam nonummy nibh euismod tincidunt ut laoreet dolore magna aliquam erat volutpat. Ut wisi enim ad minim veniam.</div></div>
  <div style="position:absolute;left:75px;top:46px;width:56px;height:88px;border-radius:9px 9px 0 0;background:linear-gradient(180deg,var(--gold-light),var(--gold) 50%,var(--gold-dark));border-bottom:2px solid var(--dark);color:#fff;text-align:center;padding-top:7px">
    <span class="dot d" style="width:10px;height:10px"></span><div style="font-size:5.4px;margin:4px 0 3px">Heading</div><div class="body-text" style="color:#fff;text-align:center;padding:0 4px">Lorem ipsum dolor sit amet, consectetuer adipiscing elit, sed diam nonummy nibh euismod tincidunt ut laoreet dolore magna aliquam erat volutpat. Ut wisi enim ad minim veniam.</div></div>
  <div style="position:absolute;left:140px;top:46px;width:110px"><div class="title-gold" style="font-weight:500;margin-bottom:6px">Curabitur Dapibus Dignissim Dui.</div><ul class="bullets body-text"><li>Lorem ipsum dolor sit amet, consectetuer adipiscing elit, sed diam nonummy nibh euismod tincidunt ut laoreet dolore magna aliquam erat volutpat. Ut wisi enim ad minim veniam.</li><li>Lorem ipsum dolor sit amet, consectetuer adipiscing elit, sed diam nonummy nibh euismod tincidunt ut laoreet dolore magna aliquam erat volutpat. Ut wisi enim ad minim veniam, quis nostrud exerci tation ullamcorper.</li><li>Lorem ipsum dolor sit amet, consectetuer adipiscing elit, sed diam nonummy nibh euismod tincidunt ut laoreet dolore magna aliquam erat volutpat. Ut wisi enim ad minim veniam, quis nostrud exerci tation.</li></ul></div>
  <div class="footer"><span class="mark"></span><span class="brand">NIVEL CREST</span><div class="bar"><span>www.nivelcrest.com</span><span>PAGE 01</span></div></div>
</section>

<!-- 12 List + icon grid -->
<section class="slide" style="left:731px;top:718px">
  <div class="heading"><b>Heading</b> Goes Here</div>
  <div style="position:absolute;left:12px;top:53px;width:110px">
    <div style="font-size:3.2px;font-weight:500">Title Goes Here</div><p class="body-text" style="margin-bottom:5px">Lorem ipsum dolor sit amet, consectetuer adipiscing elit, sed diam nonummy nibh euismod tincidunt ut laoreet dolore magna aliquam erat volutpat. Ut wisi enim ad minim veniam.</p>
    <div style="font-size:3.2px;font-weight:500">Title Goes Here</div><p class="body-text" style="margin-bottom:5px">Lorem ipsum dolor sit amet, consectetuer adipiscing elit, sed diam nonummy nibh euismod tincidunt ut laoreet dolore magna aliquam erat volutpat. Ut wisi enim ad minim veniam.</p>
    <div style="font-size:3.2px;font-weight:500">Title Goes Here</div><p class="body-text">Lorem ipsum dolor sit amet, consectetuer adipiscing elit, sed diam nonummy nibh euismod tincidunt ut laoreet dolore magna aliquam erat volutpat. Ut wisi enim ad minim veniam.</p>
  </div>
  <div style="position:absolute;left:145px;top:48px;width:106px;display:grid;grid-template-columns:1fr 1fr;gap:8px 10px;text-align:center">
    <div><span class="dot g" style="width:12px;height:12px"></span><div class="body-text" style="text-align:center;margin-top:3px">Lorem ipsum dolor sit amet, consectetuer adipiscing elit, sed diam nonummy nibh euismod tincidunt.</div></div>
    <div><span class="dot g" style="width:12px;height:12px"></span><div class="body-text" style="text-align:center;margin-top:3px">Lorem ipsum dolor sit amet, consectetuer adipiscing elit, sed diam nonummy nibh euismod tincidunt.</div></div>
    <div><span class="dot g" style="width:12px;height:12px"></span><div class="body-text" style="text-align:center;margin-top:3px">Lorem ipsum dolor sit amet, consectetuer adipiscing elit, sed diam nonummy nibh euismod tincidunt.</div></div>
    <div><span class="dot g" style="width:12px;height:12px"></span><div class="body-text" style="text-align:center;margin-top:3px">Lorem ipsum dolor sit amet, consectetuer adipiscing elit, sed diam nonummy nibh euismod tincidunt.</div></div>
  </div>
  <div class="footer"><span class="mark"></span><span class="brand">NIVEL CREST</span><div class="bar"><span>www.nivelcrest.com</span><span>PAGE 01</span></div></div>
</section>

<!-- 13 About + photos -->
<section class="slide" style="left:111px;top:920px">
  <div class="heading"><b>Heading</b> Goes Here</div>
  <div class="body-text" style="position:absolute;left:10px;top:36px;width:241px;font-size:2.7px;line-height:3.4px"><p>Nivel Crest is an independent planning consultancy that works alongside private builders and developers from the first sketch to the final handover. Our approach is simple: careful planning before the first stone is laid saves money on every stage that follows. We review designs, tenders and schedules, compare offers, and point out where costs can be reduced without any loss of quality or safety on site.</p><p style="margin-top:3px">Our team combines architects, engineers and cost planners with many years of practical experience on residential and commercial projects. We prepare clear reports, workflows and price overviews so that every client knows what to expect, and we stay at their side until the building is complete and the final accounts are settled.</p></div>
  <div style="position:absolute;left:13px;top:78px;width:237px;display:grid;grid-template-columns:repeat(3,1fr);column-gap:12px">
    <div><div role="img" aria-label="Photo of colleagues meeting at a table" style="height:34px;background:linear-gradient(135deg,#d8dde2,#5b5f66 60%,#9aa1a8)"></div><div class="title-gold" style="font-weight:500;text-align:center;margin:5px 0 4px">Heading Goes Here</div><div class="body-text" style="padding-left:8px">Lorem ipsum dolar sit amet, consectetur adipiscing edit. Vivamus eu dui ex.</div></div>
    <div><div role="img" aria-label="Photo of business person with tablet" style="height:34px;background:linear-gradient(135deg,#cfe3f3,#5d89b5 55%,#e8f1f8)"></div><div class="title-gold" style="font-weight:500;text-align:center;margin:5px 0 4px">Heading Goes Here</div><div class="body-text" style="padding-left:8px">Lorem ipsum dolar sit amet, consectetur adipiscing edit. Vivamus eu dui ex.</div></div>
    <div><div role="img" aria-label="Photo of two colleagues reviewing papers" style="height:34px;background:linear-gradient(135deg,#c6d6e6,#7c95ae 55%,#e2e9ef)"></div><div class="title-gold" style="font-weight:500;text-align:center;margin:5px 0 4px">Heading Goes Here</div><div class="body-text" style="padding-left:8px">Lorem ipsum dolar sit amet, consectetur adipiscing edit. Vivamus eu dui ex.</div></div>
  </div>
  <div class="footer"><span class="mark"></span><span class="brand">NIVEL CREST</span><div class="bar"><span>www.nivelcrest.com</span><span>PAGE 01</span></div></div>
</section>

<!-- 14 Infographic chart -->
<section class="slide" style="left:421px;top:920px">
  <div class="heading"><b>Heading</b> Goes Here</div>
  <div style="position:absolute;left:0;width:261px;top:29px;text-align:center;font-size:11px;font-weight:600;color:var(--gold)">INFOGRAPHIC CHART</div>
  <div class="body-text" style="position:absolute;left:40px;top:44px;width:181px;text-align:center">Lorem ipsum dolor sit amet, consectetuer adipiscing elit, sed diam nonummy nibh euismod tincidunt ut laoreet dolore magna aliquam erat volutpat. Ut wisi enim ad minim veniam, quis nostrud exerci tation ullamcorper suscipit lobortis nisl ut aliquip ex ea commodo consequat.</div>
  <svg style="position:absolute;left:95px;top:60px" width="72" height="72" viewBox="0 0 72 72" aria-label="Ring chart with eight 50 percent segments">
    <defs><linearGradient id="ring" x1="0" y1="0" x2="1" y2="1"><stop offset="0" stop-color="#ecc96f"/><stop offset=".5" stop-color="#c8952f"/><stop offset="1" stop-color="#8f621a"/></linearGradient><radialGradient id="core"><stop offset="0" stop-color="#8a8a8e"/><stop offset="1" stop-color="#232325"/></radialGradient></defs>
    <circle cx="36" cy="36" r="29" fill="none" stroke="url(#ring)" stroke-width="13"/>
    <circle cx="36" cy="36" r="22" fill="#fff"/>
    <circle cx="36" cy="36" r="19" fill="url(#core)"/>
    <g fill="#fff" font-family="Montserrat,sans-serif" font-size="3.4" font-weight="600" text-anchor="middle">
      <text x="36" y="10">50%</text><text x="36" y="65">50%</text>
      <text x="17" y="18">50%</text><text x="55" y="18">50%</text>
      <text x="10" y="38">50%</text><text x="62" y="38">50%</text>
      <text x="17" y="58">50%</text><text x="55" y="58">50%</text>
    </g>
    <g fill="#fff"><circle cx="36" cy="31" r="3.4"/><rect x="30" y="35" width="12" height="7" rx="3"/></g>
  </svg>
  <div style="position:absolute;left:40px;top:70px;width:50px;display:grid;row-gap:11px">
    <div class="item"><span class="dot g" style="width:8px;height:8px"></span><div class="body-text" style="font-size:2px;line-height:2.6px">Lorem ipsum dolor sit amet, consectetur adipiscing elit. Praesent non nibh.</div></div>
    <div class="item"><span class="dot g" style="width:8px;height:8px"></span><div class="body-text" style="font-size:2px;line-height:2.6px">Lorem ipsum dolor sit amet, consectetur adipiscing elit. Praesent non nibh.</div></div>
    <div class="item"><span class="dot g" style="width:8px;height:8px"></span><div class="body-text" style="font-size:2px;line-height:2.6px">Lorem ipsum dolor sit amet, consectetur adipiscing elit. Praesent non nibh.</div></div>
  </div>
  <div style="position:absolute;left:178px;top:70px;width:50px;display:grid;row-gap:11px">
    <div class="item"><span class="dot g" style="width:8px;height:8px"></span><div class="body-text" style="font-size:2px;line-height:2.6px">Lorem ipsum dolor sit amet, consectetur adipiscing elit. Praesent non nibh.</div></div>
    <div class="item"><span class="dot g" style="width:8px;height:8px"></span><div class="body-text" style="font-size:2px;line-height:2.6px">Lorem ipsum dolor sit amet, consectetur adipiscing elit. Praesent non nibh.</div></div>
    <div class="item"><span class="dot g" style="width:8px;height:8px"></span><div class="body-text" style="font-size:2px;line-height:2.6px">Lorem ipsum dolor sit amet, consectetur adipiscing elit. Praesent non nibh.</div></div>
  </div>
  <div class="footer"><span class="mark"></span><span class="brand">NIVEL CREST</span><div class="bar"><span>www.nivelcrest.com</span><span>PAGE 01</span></div></div>
</section>

<!-- 15 Thank you -->
<section class="slide" style="left:731px;top:920px">
  <div class="logo" style="top:15px"><span class="sq"></span><span class="name">NIVEL CREST</span></div>
  <div class="photo" role="img" aria-label="City skyline photograph in golden tones" style="left:0;top:41px;width:261px;height:82px"></div>
  <div style="position:absolute;left:0;width:261px;top:83px;text-align:center;font-family:'Oswald',sans-serif;font-weight:700;font-size:32px;color:#fff;line-height:1">THANK YOU!</div>
  <div style="position:absolute;left:0;width:261px;top:124px;text-align:center;font-size:8px;font-weight:500;color:var(--gold-light);line-height:1">PRESENTATION</div>
  <div style="position:absolute;left:0;width:261px;top:133px;text-align:center;font-size:4.6px;font-weight:600">TITLE GOESHERE</div>
  <div style="position:absolute;left:0;width:261px;top:150px;text-align:center;font-size:4px">www.nivelcrest.com</div>
</section>

</body>
</html>
```